Real estate broker business card

Want a modern celan but effective business card for my residential and commercial real estate business. I want the back of the card to advertise my services and to capture business. I have attached the back of my current business card fore ideas
Updates

Logos, photo and text updates added! Added Saturday, September 3, 2016

Project Deadline Extended Reason: LOGOS, PHOTOS AND TEST JUST UPLOADED! I'M READY TO PICK A DESIGN! THANK YOU! Added Saturday, September 3, 2016

Target Market(s)

home buyers and seller. commercial buyers and sellers

Industry/Entity Type

Real Estate

Contact Information for Business Card

must have my contact information and my photo

Requirements
Must have
• Carla Ventrino
• Owner & Qualifying Broker
• Ventrino Real Estate Services
• 505.718.2094
• carla@ventrinohomes.example
• www.ventrinohomes.example
Nice to have
• metallic
• Business capture text: " Don't buy or lease property without someone looking out for your best interests. I will represent you on your home or investment purchase for FREE!"
• "Home owners, call today to receive a FREE market analysis for your homes value!

```html
<!DOCTYPE html>
<html lang="en">
<head>
<meta charset="utf-8">
<title>Carla Ventrino – Business Card</title>
<link href="https://fonts.googleapis.com/css2?family=Pinyon+Script&family=Source+Sans+3:wght@400;600&display=swap" rel="stylesheet">
<style>
  :root {
    --backdrop: #161616;
    --teal-top: #1b8a9b;
    --teal-bottom: #05606f;
    --teal-ink: #0f6f7d;
    --card-light: #e0e0e0;
    --text-light: #ffffff;
    --text-dark: #3a3a3a;
    --photo-dark: #3b2a24;
    --photo-mid: #9c7a6a;
    --photo-light: #e8e2dc;
  }
  html, body {
    margin: 0;
    padding: 0;
    width: 1200px;
    height: 900px;
    overflow: hidden;
    background: var(--backdrop);
  }
  .canvas {
    position: relative;
    width: 1200px;
    height: 900px;
    font-family: "Source Sans 3", sans-serif;
  }
  .card {
    position: absolute;
    top: 184px;
    height: 490px;
    border-radius: 11px;
    overflow: hidden;
  }
  .card-front {
    left: 299px;
    width: 301px;
    background: linear-gradient(180deg, var(--teal-top) 0%, var(--teal-bottom) 100%);
    text-align: center;
  }
  .broker-name {
    margin: 96px 0 0;
    font-family: "Pinyon Script", cursive;
    font-weight: 400;
    font-size: 38px;
    line-height: 1;
    color: var(--text-light);
  }
  .broker-title {
    margin: 8px 0 0;
    font-size: 15px;
    color: var(--text-light);
  }
  .broker-photo {
    position: absolute;
    left: 38px;
    bottom: 0;
    width: 226px;
    height: 284px;
    border-radius: 110px 110px 0 0;
    background: linear-gradient(180deg, var(--photo-dark) 0%, var(--photo-mid) 55%, var(--photo-light) 100%);
  }
  .card-back {
    left: 645px;
    width: 304px;
    background: var(--card-light);
    text-align: center;
  }
  .brand-mark {
    display: block;
    margin: 98px auto 0;
  }
  .brand-name {
    margin: 14px 0 0;
    font-size: 42px;
    font-weight: 600;
    letter-spacing: 1px;
    line-height: 1;
    color: var(--teal-ink);
  }
  .brand-tagline {
    margin: 6px 0 0;
    font-size: 14px;
    font-weight: 600;
    letter-spacing: 2.6px;
    color: var(--teal-ink);
  }
  .contact-list {
    list-style: none;
    margin: 46px 0 0;
    padding: 0;
    font-size: 16px;
    line-height: 22px;
    color: var(--text-dark);
  }
  .contact-label {
    font-weight: 600;
    color: var(--teal-ink);
  }
</style>
</head>
<body>
<main class="canvas">
  <section class="card card-front">
    <h1 class="broker-name">Carla Ventrino</h1>
    <p class="broker-title">Owner &amp; Qualifying Broker</p>
    <div class="broker-photo" role="img" aria-label="Portrait photo of the broker"></div>
  </section>

  <section class="card card-back">
    <svg class="brand-mark" width="70" height="70" viewBox="0 0 70 70" aria-hidden="true">
      <circle cx="35" cy="35" r="33" fill="var(--teal-ink)"/>
    </svg>
    <p class="brand-name">VENTRINO</p>
    <p class="brand-tagline">REAL ESTATE SERVICES</p>
    <ul class="contact-list">
      <li><span class="contact-label">P:</span> 505.718.2094</li>
      <li><span class="contact-label">E:</span> carla@ventrinohomes.example</li>
      <li><span class="contact-label">W:</span> www.ventrinohomes.example</li>
    </ul>
  </section>
</main>
</body>
</html>
```